New Card and Dice Game Package Design for retail distribution

Need to create a packaging design for a new card/dice game. Below are the high level details:
Size: 93mm wide x 106mm tall x 18mm deep
*same size as a standard TOZ card box.
Design is to portray fun and humor
Attached is the creative brief. The sample image of the front is simply a basic vision. The end result should be something professional and grab the attention of gamers.
Target Market(s)
millennials, families
Industry/Entity Type
Retail
Font styles to use
Sans Serif
Colors
abd036
Requirements
Must have
- Primary background color - green
- No real photos
Nice to have
- Illustrations
Should not have
- photos

```html
<!DOCTYPE html>
<html lang="en">
<head>
<meta charset="utf-8">
<title>Rule Flip – Board Game Add-On Edition</title>
<link rel="stylesheet" href="https://fonts.googleapis.com/css2?family=Patrick+Hand+SC&display=swap">
<style>
  :root {
    --stage: #e9e9e9;
    --paper: #ffffff;
    --swirl: #e6e6e6;
    --green: #abd036;
    --green-light: #c6e06a;
    --yellow: #f5ee1a;
    --ink: #141414;
    --die-red: #d9363e;
    --pip: #ffffff;
    --card-white: #fbfbfb;
    --card-edge: #d4d4d4;
  }
  * { margin: 0; padding: 0; box-sizing: border-box; }
  html, body {
    width: 960px;
    height: 1200px;
    overflow: hidden;
    background: var(--stage);
  }
  body {
    font-family: "Patrick Hand SC", "Comic Sans MS", sans-serif;
    color: var(--ink);
  }
  .package {
    position: absolute;
    left: 70px;
    top: 208px;
    width: 821px;
    height: 784px;
    display: flex;
    box-shadow: 0 12px 34px rgba(0,0,0,0.14);
  }

  /* ---------- side panel ---------- */
  .package-spine {
    position: relative;
    width: 133px;
    height: 100%;
    background: linear-gradient(180deg, var(--green) 0%, var(--green-light) 55%, var(--green) 100%);
    overflow: hidden;
  }
  .spine-facts {
    position: absolute;
    top: 22px;
    left: 0;
    width: 100%;
    text-align: center;
    font-size: 16px;
    line-height: 1.1;
  }
  .spine-slogan {
    position: absolute;
    top: 150px;
    left: 50%;
    transform: translateX(-50%);
    writing-mode: vertical-rl;
    font-size: 22px;
    line-height: 1.1;
    white-space: nowrap;
  }
  .spine-dice {
    position: absolute;
    top: 370px;
    left: 26px;
    width: 80px;
    height: 130px;
  }
  .spine-brand {
    position: absolute;
    bottom: 40px;
    left: 50%;
    transform: translateX(-50%);
    writing-mode: vertical-rl;
    font-size: 46px;
    line-height: 1;
    white-space: nowrap;
  }
  .spine-brand .brand-dot {
    display: inline-block;
    width: 14px;
    height: 14px;
    border-radius: 50%;
    background: var(--ink);
    margin-top: 8px;
  }

  /* ---------- front panel ---------- */
  .package-front {
    position: relative;
    width: 688px;
    height: 100%;
    background: var(--paper);
    overflow: hidden;
  }
  .backdrop {
    position: absolute;
    inset: 0;
    width: 100%;
    height: 100%;
  }
  .tagline {
    position: absolute;
    top: 78px;
    right: 36px;
    width: 360px;
    font-size: 38px;
    line-height: 1.05;
    text-align: center;
    transform: rotate(-4deg);
  }
  .brand-name {
    position: absolute;
    left: 80px;
    top: 262px;
    width: 560px;
    text-align: center;
    font-size: 150px;
    line-height: 0.9;
    font-weight: 400;
    transform: rotate(-3deg);
  }
  .brand-name .brand-dot {
    display: inline-block;
    width: 30px;
    height: 30px;
    border-radius: 50%;
    background: var(--green);
    vertical-align: middle;
    margin-left: 12px;
  }
  .front-facts {
    position: absolute;
    left: 66px;
    bottom: 34px;
    font-size: 17px;
    line-height: 1.15;
    text-align: center;
  }
  .edition {
    position: absolute;
    right: 24px;
    bottom: 48px;
    font-size: 34px;
    line-height: 1.05;
    text-align: right;
    transform: rotate(-4deg);
  }
</style>
</head>
<body>
  <div class="package">

    <aside class="package-spine">
      <p class="spine-facts">Ages 7+<br>2-6 Players<br>Family</p>
      <p class="spine-slogan">Your House. Your Rules.</p>
      <svg class="spine-dice" viewBox="0 0 80 130" role="img" aria-label="Four small red dice">
        <g fill="var(--die-red)">
          <rect x="4" y="6" width="30" height="30" rx="6" transform="rotate(-10 19 21)"/>
          <rect x="44" y="0" width="30" height="30" rx="6" transform="rotate(8 59 15)"/>
          <rect x="6" y="88" width="30" height="30" rx="6" transform="rotate(12 21 103)"/>
          <rect x="44" y="72" width="30" height="30" rx="6" transform="rotate(-8 59 87)"/>
        </g>
        <g fill="var(--pip)">
          <circle cx="13" cy="14" r="3"/><circle cx="25" cy="28" r="3"/>
          <circle cx="52" cy="8" r="3"/><circle cx="59" cy="15" r="3"/><circle cx="66" cy="22" r="3"/>
          <circle cx="14" cy="96" r="3"/><circle cx="28" cy="96" r="3"/><circle cx="14" cy="110" r="3"/><circle cx="28" cy="110" r="3"/>
          <circle cx="59" cy="87" r="3"/>
        </g>
      </svg>
      <p class="spine-brand">Rule Flip<span class="brand-dot"></span></p>
    </aside>

    <main class="package-front">
      <svg class="backdrop" viewBox="0 0 688 784" preserveAspectRatio="none">
        <defs>
          <radialGradient id="swirlGlow" cx="0.72" cy="0.38" r="0.65">
            <stop offset="0" stop-color="var(--paper)"/>
            <stop offset="0.5" stop-color="var(--swirl)"/>
            <stop offset="1" stop-color="var(--paper)"/>
          </radialGradient>
          <linearGradient id="greenFade" x1="0" y1="0" x2="1" y2="1">
            <stop offset="0" stop-color="var(--green)"/>
            <stop offset="1" stop-color="var(--green-light)"/>
          </linearGradient>
        </defs>
        <rect class="swirl-pattern" x="0" y="0" width="688" height="784" fill="url(#swirlGlow)" role="img" aria-label="Soft grey swirl pattern behind the artwork"/>
        <polygon class="green-panel" points="0,40 380,400 160,784 0,784" fill="url(#greenFade)"/>
        <polygon class="yellow-stripe" points="380,400 430,430 220,784 160,784" fill="var(--yellow)" opacity="0.8"/>
        <polygon class="yellow-panel" points="200,784 688,500 688,784" fill="var(--yellow)"/>

        <g class="card-fan" role="img" aria-label="Fan of blank white game cards" fill="var(--card-white)" stroke="var(--card-edge)" stroke-width="2">
          <rect x="120" y="560" width="150" height="200" rx="10" transform="rotate(-24 195 760)"/>
          <rect x="140" y="550" width="150" height="200" rx="10" transform="rotate(-14 215 750)"/>
          <rect x="165" y="545" width="150" height="200" rx="10" transform="rotate(-5 240 745)"/>
          <rect x="195" y="545" width="150" height="200" rx="10" transform="rotate(4 270 745)"/>
          <rect x="225" y="550" width="150" height="200" rx="10" transform="rotate(12 300 750)"/>
        </g>

        <g class="dice-pair" role="img" aria-label="Two red dice with white pips">
          <g transform="rotate(-8 475 585)">
            <rect x="430" y="540" width="90" height="90" rx="16" fill="var(--die-red)"/>
            <g fill="var(--pip)">
              <circle cx="452" cy="562" r="7"/><circle cx="498" cy="562" r="7"/>
              <circle cx="475" cy="585" r="7"/>
              <circle cx="452" cy="608" r="7"/><circle cx="498" cy="608" r="7"/>
            </g>
          </g>
          <g transform="rotate(10 590 555)">
            <rect x="535" y="500" width="110" height="110" rx="20" fill="var(--die-red)"/>
            <g fill="var(--pip)">
              <circle cx="562" cy="527" r="8"/><circle cx="618" cy="527" r="8"/>
              <circle cx="590" cy="555" r="8"/>
              <circle cx="562" cy="583" r="8"/><circle cx="618" cy="583" r="8"/>
            </g>
          </g>
        </g>
      </svg>

      <p class="tagline">Add hilarious<br>house rules to<br>any board game</p>

      <h1 class="brand-name">Rule<br>Flip<span class="brand-dot"></span></h1>

      <p class="front-facts">Ages 7+<br>2-6 Players<br>Family</p>

      <p class="edition">Board Game<br>Add-On Edition</p>
    </main>

  </div>
</body>
</html>
```